Wordpress Website Update - Elementor

I'm currently using Elementor and would like my site to be updated. A nice facelift to the current pages. We are a small boutique animation service company.
I have a list of similar production houses to use as references and would like the format/style of the site not to feel so corporate and infuse the fun that we bring to working with clients on animated projects.

Additionally, I'd like to add 2 more pages focusing on more portfolio work and Original IP - which is now our primary goal to sell our show ideas. Maybe have a password projected behind an image showcasing the show/ film. Go to our current site to review. www.pebblemoatfilms.com

Animation/ Commercials/ Vorlica/ Quelbar/ Durno/ KVT - Okay with first page being shorter and not as long as well. Have contact us 'above the fold' on options as well.

Animation and Film

• Current 3 pages - additional 2 - we can focus on layout and arrangement with temporary images then swap with real assets when ready.
• site examples: pirtolstudios.com, Mardle House, Fenra Studios, Gorbleck.net, Quillstone Animation, Brindlemop Animation Studios, ZaZe Studios use Varkel Plus as inspiration.

```html
<!DOCTYPE html>
<html lang="en">
<head>
<meta charset="utf-8">
<title>Pebblemoat Films</title>
<link rel="stylesheet" href="https://fonts.googleapis.com/css2?family=Poppins:wght@400;500;600;700&family=Ubuntu:wght@500;700&display=swap">
<style>
:root{
  --navy:#1e1b33;
  --white:#ffffff;
  --purple:#5b2bc0;
  --violet:#7a55e6;
  --lavender:#9c82f0;
  --red:#e8214f;
  --cream:#eef4ee;
  --ink:#1e1b33;
  --logo-grey:#b9b8c6;
  --dot:rgba(255,255,255,.16);
}
*{margin:0;padding:0;box-sizing:border-box}
html,body{width:1200px;height:3086px;overflow:hidden}
body{background:var(--navy);font-family:"Poppins",sans-serif;color:var(--white);position:relative}
.abs{position:absolute}

/* header */
.site-header{position:absolute;left:0;top:0;width:1200px;height:92px;background:var(--navy)}
.nav-link{position:absolute;top:35px;font-weight:600;font-size:19px;color:var(--white);text-decoration:none;line-height:1}
.brand{position:absolute;left:470px;top:18px;width:260px;text-align:center}
.brand-name{font-family:"Ubuntu",sans-serif;font-weight:700;font-size:36px;color:var(--violet);line-height:1;letter-spacing:-.5px}
.brand-tag{font-size:9px;font-weight:600;letter-spacing:9px;color:var(--red);margin-top:5px;padding-left:9px}
.socials{position:absolute;display:flex;gap:7px}
.social{width:30px;height:30px;border:1.5px solid var(--lavender);border-radius:50%;display:flex;align-items:center;justify-content:center}
.social i{width:8px;height:8px;border-radius:50%;background:var(--lavender)}

/* shared art */
.art{position:absolute;overflow:hidden}
.art::after{content:"";position:absolute;inset:0;box-shadow:inset 0 0 60px rgba(10,8,30,.35);pointer-events:none}

/* hero */
.hero{position:absolute;left:0;top:92px;width:1200px;height:620px}
.arrow{position:absolute}

/* section heads */
.section-head{position:absolute;background-image:radial-gradient(var(--dot) 1.2px,transparent 1.4px);background-size:8px 8px}
.section-title{font-family:"Ubuntu",sans-serif;font-weight:700;font-size:44px;color:var(--white);position:absolute;line-height:1.1;letter-spacing:.5px}
.pager{position:absolute;display:flex;gap:10px}

/* ip cards */
.ip-card{position:absolute;top:888px;width:243px}
.ip-art{position:relative;width:243px;height:174px;border-radius:10px;overflow:hidden}
.ip-caption{margin-top:14px;font-size:16px;font-weight:500;line-height:1.2}

/* feature band */
.feature{position:absolute;top:1178px;width:400px;height:418px}
.feature-art{position:relative;height:282px;overflow:hidden}
.feature-text{height:136px;padding:22px 0 0 75px}
.feature-title{font-family:"Ubuntu",sans-serif;font-weight:700;font-size:29px;line-height:1.1;letter-spacing:.5px}
.feature-sub{font-size:16px;line-height:1.55;margin-top:8px;max-width:270px}

/* projects */
.eyebrow{position:absolute;left:0;width:1200px;text-align:center;top:1676px;color:var(--red);font-size:18px}
.btn{position:absolute;display:flex;align-items:center;justify-content:center;border-radius:26px;background:linear-gradient(90deg,var(--red),var(--purple));color:var(--white);font-weight:600;font-size:19px;text-decoration:none}

/* clients */
.client{position:absolute;top:2460px;height:44px;font-weight:700;font-size:28px;color:var(--logo-grey);display:flex;align-items:center;gap:8px;letter-spacing:.5px}
.client .mark{width:22px;height:22px;border-radius:50%;background:var(--logo-grey)}

/* mascots */
.mascot{position:absolute;overflow:hidden}

/* cta */
.cta{position:absolute;left:0;top:2643px;width:1200px;height:335px;background:var(--cream)}
.cta-title{position:absolute;left:76px;top:90px;font-family:"Ubuntu",sans-serif;font-weight:700;font-size:43px;color:var(--ink);letter-spacing:.5px}
.cta-sub{position:absolute;left:75px;top:148px;font-size:19px;color:var(--ink)}

/* footer */
.site-footer{position:absolute;left:0;top:2978px;width:1200px;height:108px;background:var(--navy)}
.copyright{position:absolute;left:76px;top:46px;font-size:13px}
</style>
</head>
<body>

<header class="site-header">
  <a class="nav-link" style="left:74px">Home</a>
  <a class="nav-link" style="left:176px">About Us</a>
  <a class="nav-link" style="left:309px">Services</a>
  <div class="brand"><div class="brand-name">PEBBLEMOAT</div><div class="brand-tag">FILMS</div></div>
  <a class="nav-link" style="left:752px;top:35px">Projects</a>
  <a class="nav-link" style="left:877px;top:35px">Contact</a>
  <div class="socials" style="left:984px;top:31px">
    <span class="social" aria-label="Social link one"><i></i></span><span class="social" aria-label="Social link two"><i></i></span><span class="social" aria-label="Social link three"><i></i></span><span class="social" aria-label="Social link four"><i></i></span>
  </div>
</header>

<section class="hero">
  <svg width="1200" height="620" viewBox="0 0 1200 620" role="img" aria-label="Collage of four animated stills: divers under the sea, a fluffy puppy with headset, a giraffe in glasses, and a girl playing harmonica">
    <defs>
      <radialGradient id="sea" cx=".35" cy=".25" r=".9"><stop offset="0" stop-color="#5fc0f0"/><stop offset=".45" stop-color="#1f78c0"/><stop offset="1" stop-color="#0b2c5e"/></radialGradient>
      <radialGradient id="pup" cx=".55" cy=".3" r=".8"><stop offset="0" stop-color="#f2b6d4"/><stop offset=".35" stop-color="#c26fd0"/><stop offset=".7" stop-color="#8a4ee0"/><stop offset="1" stop-color="#5a2aa8"/></radialGradient>
      <radialGradient id="gir" cx=".6" cy=".45" r=".75"><stop offset="0" stop-color="#c8a276"/><stop offset=".4" stop-color="#8c6e50"/><stop offset=".8" stop-color="#4a4440"/><stop offset="1" stop-color="#2e2c2c"/></radialGradient>
      <linearGradient id="kid" x1="0" y1="0" x2="0" y2="1"><stop offset="0" stop-color="#3e63c0"/><stop offset=".45" stop-color="#6a4a7a"/><stop offset=".7" stop-color="#b24a3c"/><stop offset="1" stop-color="#e0527a"/></linearGradient>
      <radialGradient id="kidlight" cx=".35" cy=".75" r=".4"><stop offset="0" stop-color="#f0a070" stop-opacity=".7"/><stop offset="1" stop-color="#f0a070" stop-opacity="0"/></radialGradient>
    </defs>
    <rect width="1200" height="620" fill="url(#sea)"/>
    <polygon points="216,0 988,0 600,310" fill="url(#pup)"/>
    <polygon points="988,0 1200,0 1200,620 988,620 600,310" fill="url(#gir)"/>
    <polygon points="216,620 988,620 600,310" fill="url(#kid)"/>
    <polygon points="216,620 988,620 600,310" fill="url(#kidlight)"/>
    <path d="M216 0L600 310 216 620M988 0L600 310 988 620" stroke="#1e1b33" stroke-opacity=".35" stroke-width="2" fill="none"/>
  </svg>
  <svg class="arrow" style="left:36px;top:290px" width="40" height="40" viewBox="0 0 40 40"><path d="M36 20H6M18 7L5 20l13 13" stroke="#fff" stroke-width="4" fill="none" opacity=".85"/></svg>
  <svg class="arrow" style="left:1140px;top:290px" width="40" height="40" viewBox="0 0 40 40"><path d="M4 20h30M22 7l13 13-13 13" stroke="#fff" stroke-width="4" fill="none" opacity=".85"/></svg>
</section>

<div class="section-head" style="left:80px;top:785px;width:1045px;height:70px"></div>
<h2 class="section-title" style="left:86px;top:794px">Pebblemoat Original IP</h2>
<div class="pager" style="left:1068px;top:809px">
  <svg width="26" height="24" viewBox="0 0 26 24"><path d="M24 12H3M12 3L3 12l9 9" stroke="#fff" stroke-width="3" fill="none"/></svg>
  <svg width="26" height="24" viewBox="0 0 26 24"><path d="M2 12h21M14 3l9 9-9 9" stroke="#e8214f" stroke-width="3" fill="none"/></svg>
</div>

<div class="ip-card" style="left:74px"><div class="ip-art" role="img" aria-label="Elf beside a festive slot machine" style="background:radial-gradient(circle at 72% 45%,#f2c25a 0,#c8302a 38%,transparent 62%),radial-gradient(circle at 20% 60%,#7ab848 0,#2f7a34 45%,transparent 70%),linear-gradient(135deg,#f0dcc0,#8a1e1e)"></div><p class="ip-caption">Neque porro quisquam</p></div>
<div class="ip-card" style="left:345px"><div class="ip-art" role="img" aria-label="Pencil sketch of a city skyline" style="background:radial-gradient(ellipse at 50% 30%,#ffffff 0,#e4e4e4 40%,transparent 70%),linear-gradient(180deg,#d8d8d8 0,#bcbcbc 55%,#6e6e6e 100%)"></div><p class="ip-caption">Neque porro quisquam</p></div>
<div class="ip-card" style="left:614px"><div class="ip-art" role="img" aria-label="Glowing blue crystal cave with a ship" style="background:radial-gradient(circle at 55% 40%,#9ad4ff 0,#4a7fe8 25%,transparent 55%),radial-gradient(circle at 20% 80%,#3a2a9a 0,transparent 50%),linear-gradient(160deg,#2a1e78,#1a2a8a 50%,#0e0c3a)"></div><p class="ip-caption">Neque porro quisquam</p></div>
<div class="ip-card" style="left:885px"><div class="ip-art" role="img" aria-label="Storyboard panel grid" style="background:linear-gradient(90deg,transparent 32%,#1e1b33 32%,#1e1b33 33%,transparent 33%,transparent 66%,#1e1b33 66%,#1e1b33 67%,transparent 67%),linear-gradient(180deg,transparent 32%,#1e1b33 32%,#1e1b33 34%,transparent 34%,transparent 66%,#1e1b33 66%,#1e1b33 68%,transparent 68%),linear-gradient(135deg,#f4f4f4,#9a9a9a)"></div><p class="ip-caption">Neque porro quisquam</p></div>

<div class="feature" style="left:0">
  <div class="feature-art" role="img" aria-label="Smiling sloth hanging in a playroom" style="background:radial-gradient(ellipse at 68% 55%,#e0d2b8 0,#b49c7c 35%,transparent 65%),radial-gradient(circle at 95% 15%,#d84a4a 0,transparent 25%),linear-gradient(135deg,#6e5a44,#a08a6c 50%,#3e7a78)"></div>
  <div class="feature-text" style="background:var(--purple)"><div class="feature-title">Animation Reel</div><div class="feature-sub">Story and Animation is where PMF thrives.</div></div>
</div>
<div class="feature" style="left:400px">
  <div class="feature-art" role="img" aria-label="Three giraffes in a sunny room" style="background:radial-gradient(ellipse at 25% 25%,#f4efe4 0,#cfc4b0 30%,transparent 55%),radial-gradient(ellipse at 55% 70%,#b88a58 0,#8a6440 40%,transparent 70%),linear-gradient(135deg,#bdb2a0,#6a5440 60%,#3a2e24)"></div>
  <div class="feature-text" style="background:var(--red);padding-left:25px"><div class="feature-title">Giraffes &amp; Kids Are Free!</div><div class="feature-sub">Fresh Out The Render Oven. Careful It's</div></div>
</div>
<div class="feature" style="left:800px">
  <div class="feature-art" role="img" aria-label="Artists working at editing screens" style="background:radial-gradient(ellipse at 75% 45%,#8aa8d8 0,#4a62a8 30%,transparent 60%),linear-gradient(0deg,#2ac0e0 0,transparent 18%),linear-gradient(135deg,#2a2458,#3a4a88 55%,#141c3a)"></div>
  <div class="feature-text" style="background:var(--lavender);padding-left:24px"><div class="feature-title">Our Expertise</div><div class="feature-sub">Creative Experts That Solve Problems</div></div>
</div>
<svg class="arrow" style="left:36px;top:1322px" width="40" height="40" viewBox="0 0 40 40"><path d="M36 20H6M18 7L5 20l13 13" stroke="#fff" stroke-width="4" fill="none" opacity=".85"/></svg>
<svg class="arrow" style="left:1140px;top:1322px" width="40" height="40" viewBox="0 0 40 40"><path d="M4 20h30M22 7l13 13-13 13" stroke="#fff" stroke-width="4" fill="none" opacity=".85"/></svg>

<div class="section-head" style="left:345px;top:1664px;width:515px;height:102px"></div>
<p class="eyebrow">Just A Few</p>
<h2 class="section-title" style="left:0;width:1200px;text-align:center;top:1704px">Our Projects</h2>
<div class="mascot" role="img" aria-label="Purple furry monster character with a big grin" style="left:1018px;top:1605px;width:182px;height:295px;border-radius:48% 0 0 38% / 40% 0 0 30%;background:radial-gradient(circle at 40% 35%,#c4a4ff 0,#9a6af4 30%,#7440e0 60%,#5a2bc0 100%)"></div>

<div class="art" role="img" aria-label="Blue robot character turnaround" style="left:0;top:1900px;width:206px;height:188px;background:radial-gradient(circle at 25% 35%,#b8e0ff 0,#5aa4e4 30%,transparent 50%),radial-gradient(circle at 78% 35%,#b8e0ff 0,#5aa4e4 30%,transparent 50%),linear-gradient(180deg,#0e0e18 0,#0e0e18 55%,#4a9ad8 56%,#2a6ab0 100%)"></div>
<div class="art" role="img" aria-label="Parade crowd with a banner" style="left:216px;top:1800px;width:206px;height:189px;background:linear-gradient(180deg,transparent 48%,#e8e8f0 48%,#e8e8f0 70%,transparent 70%),radial-gradient(ellipse at 50% 20%,#8ac4e8 0,transparent 60%),linear-gradient(180deg,#6a9ac0,#7a6a7a 60%,#5a5a60)"></div>
<div class="art" role="img" aria-label="Divers under the sea" style="left:216px;top:1998px;width:206px;height:190px;background:radial-gradient(circle at 40% 20%,#7ed0f8 0,#2e88d0 40%,transparent 75%),linear-gradient(180deg,#2a8ad0,#0e3a72)"></div>
<div class="art" role="img" aria-label="Giraffe wearing glasses" style="left:433px;top:1800px;width:333px;height:388px;background:radial-gradient(ellipse at 58% 55%,#c89e6c 0,#9a7650 30%,transparent 60%),linear-gradient(90deg,#3c3c40,#7a7672 50%,#5a4a3c)"></div>
<div class="art" role="img" aria-label="Town street and green field" style="left:778px;top:1800px;width:206px;height:189px;background:linear-gradient(180deg,#d8ecf8 0,#b8d4e8 45%,#8a9a80 50%,#7ab050 62%,#4a8a30 100%)"></div>
<div class="art" role="img" aria-label="Forest path with a small character" style="left:778px;top:1998px;width:206px;height:190px;background:radial-gradient(ellipse at 50% 60%,#f4f4f0 0,#d8e8e8 25%,transparent 45%),radial-gradient(circle at 85% 30%,#c88a40 0,transparent 40%),linear-gradient(135deg,#4a9a48,#2e7a38 60%,#6aaa4a)"></div>
<div class="art" role="img" aria-label="Animated professor beside a presenter" style="left:995px;top:1900px;width:205px;height:188px;background:radial-gradient(circle at 25% 50%,#e0dcd8 0,#a8a0a0 35%,transparent 55%),radial-gradient(ellipse at 78% 60%,#3a3030 0,transparent 45%),linear-gradient(90deg,#9a98a4,#e4ddd4)"></div>

<a class="btn" style="left:489px;top:2226px;width:222px;height:50px">View All Projects</a>

<div class="section-head" style="left:80px;top:2352px;width:1045px;height:70px"></div>
<h2 class="section-title" style="left:86px;top:2361px">Our Clients</h2>
<div class="pager" style="left:1068px;top:2376px">
  <svg width="26" height="24" viewBox="0 0 26 24"><path d="M24 12H3M12 3L3 12l9 9" stroke="#fff" stroke-width="3" fill="none"/></svg>
  <svg width="26" height="24" viewBox="0 0 26 24"><path d="M2 12h21M14 3l9 9-9 9" stroke="#e8214f" stroke-width="3" fill="none"/></svg>
</div>
<div class="client" style="left:75px">NORVANE</div>
<div class="client" style="left:248px">tekwell</div>
<div class="client" style="left:453px"><span class="mark"></span>ORALIS</div>
<div class="client" style="left:614px">BRENFIELD</div>
<div class="client" style="left:776px"><span class="mark" style="width:40px;height:40px"></span>Corvex</div>
<div class="client" style="left:980px;font-size:21px"><span class="mark" style="border-radius:4px;width:32px;height:32px"></span>Lumio Expo</div>

<section class="cta">
  <h2 class="cta-title">Why Wait Let's Co-Create!</h2>
  <p class="cta-sub">No need to scroll, save your finger and drop us a line.</p>
  <a class="btn" style="left:76px;top:194px;width:180px;height:50px">Contact Us</a>
</section>
<div class="mascot" role="img" aria-label="Green furry monster character with arms raised and a big grin" style="left:800px;top:2560px;width:360px;height:380px;border-radius:46% 46% 44% 44% / 40% 40% 52% 52%;background:radial-gradient(circle at 45% 40%,#c8ec7a 0,#9ad048 30%,#6aac2c 65%,#4a8a1e 100%)"></div>
<div class="abs" style="left:830px;top:2920px;width:300px;height:24px;border-radius:50%;background:rgba(120,80,200,.18)"></div>

<footer class="site-footer">
  <p class="copyright">Copyright © 2022 Pebblemoat Films. All rights reserved.</p>
  <div class="brand" style="top:28px"><div class="brand-name" style="font-size:30px">PEBBLEMOAT</div><div class="brand-tag">FILMS</div></div>
  <div class="socials" style="left:984px;top:39px">
    <span class="social" aria-label="Social link one"><i></i></span><span class="social" aria-label="Social link two"><i></i></span><span class="social" aria-label="Social link three"><i></i></span><span class="social" aria-label="Social link four"><i></i></span>
  </div>
</footer>

</body>
</html>
```